Southern Plantskills Academy needs a modern website that oozes professionalism

Our current website is boring and looks like everyone elses. We need a modern website that says we are the best at plant operator training. We use Brontovex and Hiraketo equipment for our training. We train all over Australia in Civil Construction, Mining and Quarrying. We want to be the "Go to" website for all plant operator training in Australia.

Industry/Entity Type

Heavy Machinery Training

Colors
0054AA
0677BA
7BADD7
CADEEF
E8F1F8
FFF300
FFF600
FEFA6F
FFFEC7
FFFEE8

```html
<!DOCTYPE html>
<html lang="en">
<head>
<meta charset="utf-8">
<title>Southern Plantskills Academy</title>
<link href="https://fonts.googleapis.com/css2?family=Rubik:wght@500;600;700&family=Roboto:wght@400;500;700&display=swap" rel="stylesheet">
<style>
:root{
  --navy:#0c2569;
  --navy-deep:#0a1f5c;
  --yellow:#f7d000;
  --yellow-band:#e8c400;
  --cream:#fdfbec;
  --text:#4a4a4a;
  --white:#ffffff;
}
*{box-sizing:border-box;margin:0;padding:0}
html,body{width:1200px;height:5029px;overflow:hidden}
body{font-family:"Roboto",Arial,sans-serif;color:var(--text);background:var(--white);position:relative}
.abs{position:absolute}
h1,h2,h3,.rubik{font-family:"Rubik",Arial,sans-serif}
.btn{position:absolute;display:flex;align-items:center;justify-content:center;border-radius:30px;font-family:"Rubik",Arial,sans-serif;font-weight:600;font-size:13px;text-transform:uppercase;color:var(--navy);background:var(--yellow)}
.btn-outline{background:var(--white);border:2px solid var(--yellow)}
.brand{left:112px;top:34px;display:flex;align-items:center;gap:12px}
.brand-mark{width:46px;height:46px;border-radius:50%;background:var(--navy)}
.brand-name{font-family:"Rubik",Arial,sans-serif;font-weight:700;font-size:17px;color:var(--navy);line-height:1.1;text-transform:uppercase}
.call{left:950px;top:40px;font-family:"Rubik",Arial,sans-serif;color:var(--navy)}
.call small{display:block;font-size:11px;color:#666}
.call strong{font-size:22px;font-weight:600}
.nav{left:0;top:117px;width:1200px;height:46px;background:var(--navy)}
.nav ul{list-style:none;display:flex;gap:27px;position:absolute;left:112px;top:15px}
.nav li{font-family:"Rubik",Arial,sans-serif;font-weight:600;font-size:12px;color:var(--white)}
.nav li.active{color:var(--yellow);border-bottom:2px solid var(--yellow);padding-bottom:3px}
.social{display:flex;gap:6px}
.social span{width:30px;height:30px;border-radius:50%;background:var(--yellow);display:block}
.hero-title{left:112px;top:290px;font-size:42px;font-weight:700;color:var(--white);line-height:52px;text-transform:uppercase;letter-spacing:1px}
.hero-text{left:112px;top:458px;width:410px;font-size:19px;color:var(--white);line-height:30px}
.sec-title{font-size:37px;font-weight:700;color:var(--navy);text-transform:uppercase;line-height:46px}
.para{font-size:14.5px;line-height:27px;text-align:justify}
.center{text-align:center}
.course{position:absolute;width:240px;text-align:center}
.course .ring{width:210px;height:210px;margin:0 auto;border-radius:50%;border:2px solid var(--yellow);padding:12px;background:var(--white)}
.course .ring div{width:100%;height:100%;border-radius:50%}
.course h3{font-size:17px;font-weight:600;color:var(--navy);margin-top:34px;line-height:26px;text-transform:uppercase}
.course .book{display:inline-block;margin-top:12px;background:var(--yellow);border-radius:20px;padding:8px 20px;font-family:"Rubik",Arial,sans-serif;font-size:9px;font-weight:600;color:var(--navy)}
.arrow{width:36px;height:36px;border-radius:50%;display:flex;align-items:center;justify-content:center}
.card{position:absolute;top:4280px;width:295px;height:263px;background:var(--white);border-radius:14px;box-shadow:0 4px 22px rgba(0,0,0,.08);text-align:center}
.card .icon{width:90px;height:90px;border-radius:50%;background:var(--yellow);margin:48px auto 0;display:flex;align-items:center;justify-content:center}
.card h3{font-size:17px;font-weight:600;color:var(--navy);margin-top:26px;text-transform:uppercase}
.card p{font-size:16px;line-height:26px;margin-top:10px;padding:0 30px;color:#444}
.photo{position:absolute;border-radius:10px}
.footer{left:0;top:4650px;width:1200px;height:379px;background:var(--navy)}
.fcol{position:absolute;top:85px;color:var(--white)}
.fcol h4{font-family:"Rubik",Arial,sans-serif;font-weight:600;font-size:16px;text-transform:uppercase;margin-bottom:14px}
.fcol li{list-style:none;display:flex;align-items:flex-start;gap:16px;font-size:13px;margin-bottom:22px}
.fcol li svg{flex:none;margin-top:1px}
.fcol .info{font-size:11px;line-height:22px;font-weight:400}
.fcol .info b{display:block;font-size:14px;font-weight:500}
.fbottom{position:absolute;left:112px;top:4985px;width:976px;border-top:1px solid rgba(255,255,255,.25)}
.copy{left:0;top:5001px;width:1200px;text-align:center;color:var(--white);font-size:12px}
</style>
</head>
<body>

<div class="abs brand"><span class="brand-mark"></span><span class="brand-name">Southern Plantskills<br>Academy</span></div>
<a class="btn" style="left:460px;top:37px;width:200px;height:48px">Course Calendar</a>
<a class="btn btn-outline" style="left:665px;top:37px;width:197px;height:48px">Student Handbook</a>
<svg class="abs" style="left:885px;top:38px" width="46" height="46" viewBox="0 0 46 46"><circle cx="23" cy="23" r="22" fill="#fff" stroke="#eee"/><path d="M16 14c2-1 3 0 4 2l1 3c0 1-1 2-2 2 1 3 3 5 6 6 0-1 1-2 2-2l3 1c2 1 3 2 2 4-1 2-3 3-5 2-6-2-10-6-12-12-1-2 0-5 1-6z" fill="#f7d000"/></svg>
<div class="abs call"><small>CALL US:</small><strong>1300 555 014</strong></div>

<nav class="abs nav">
  <ul><li class="active">HOME</li><li>ABOUT</li><li>COURSES</li><li>ONSITE / PRIVATE COURSES</li><li>ONLINE TRAINING</li><li>OUR SERVICES</li><li>STUDENT INFORMATION</li></ul>
  <div class="social abs" style="left:988px;top:8px"><span></span><span></span><span></span></div>
</nav>

<svg class="abs" style="left:0;top:163px" width="1200" height="700" viewBox="0 0 1200 700" role="img" aria-label="Excavator loading a haul truck at an open-cut mine under a blue cloudy sky">
  <defs>
    <linearGradient id="heroSky" x1="0" y1="0" x2="0" y2="1">
      <stop offset="0" stop-color="#4f7fb8"/><stop offset=".45" stop-color="#8b9fb4"/><stop offset=".7" stop-color="#6b5e4e"/><stop offset="1" stop-color="#3d3428"/>
    </linearGradient>
    <linearGradient id="heroShade" x1="0" y1="0" x2="1" y2="0">
      <stop offset="0" stop-color="#000" stop-opacity=".45"/><stop offset=".55" stop-color="#000" stop-opacity="0"/>
    </linearGradient>
  </defs>
  <path d="M1200 470 C1080 640 860 690 720 690 C420 690 160 590 0 495 L0 480 C160 560 420 668 720 668 C880 668 1060 620 1200 420 Z" fill="#f7d000"/>
  <path d="M0 0 H1200 V420 C1060 620 880 668 720 668 C420 668 160 560 0 480 Z" fill="url(#heroSky)"/>
  <path d="M0 0 H1200 V420 C1060 620 880 668 720 668 C420 668 160 560 0 480 Z" fill="url(#heroShade)"/>
</svg>
<h1 class="abs hero-title">Training and<br>experience you<br>can rely on</h1>
<p class="abs hero-text">Southern Plantskills Academy is a versatile team of passionate Health, Safety and Training professionals</p>
<a class="btn" style="left:112px;top:578px;width:140px;height:46px">Get Started</a>

<svg class="abs" style="left:112px;top:937px" width="470" height="470" viewBox="0 0 470 470" role="img" aria-label="Hand holding a white hard hat and hi-vis vest against the sun">
  <defs><radialGradient id="aboutGlow" cx=".3" cy=".4" r=".8"><stop offset="0" stop-color="#fff7d6"/><stop offset=".4" stop-color="#c9c3a0"/><stop offset="1" stop-color="#5d6f6f"/></radialGradient></defs>
  <circle cx="235" cy="235" r="228" fill="none" stroke="#0c2569" stroke-width="10"/>
  <circle cx="235" cy="235" r="216" fill="url(#aboutGlow)"/>
</svg>
<h2 class="abs sec-title" style="left:640px;top:946px">We live and<br>breathe safety</h2>
<div class="abs" style="left:640px;top:1060px;width:450px">
  <p class="para">Southern Plantskills Academy is a versatile team of passionate Health, Safety and Training professionals, all striving towards the common goal of achieving no harm to people, assets and the environment. Our experienced team have been servicing the Bowen Basin mining industry for over 10 years and we have trainers based throughout Queensland.</p>
  <p class="para" style="margin-top:10px">During this time we have established a solid reputation for delivering thorough, timely, and efficient services that are specifically tailored to meet the individual</p>
</div>
<a class="btn" style="left:640px;top:1342px;width:140px;height:46px">Learn More</a>

<section class="abs" style="left:0;top:1525px;width:1200px;height:548px;background:var(--cream)">
  <h2 class="abs sec-title center" style="left:0;top:58px;width:1200px">Our Courses</h2>
  <div class="abs arrow" style="left:37px;top:237px;background:#e6e6e6"><svg width="12" height="12" viewBox="0 0 12 12"><path d="M8 1 3 6l5 5" stroke="#333" stroke-width="2" fill="none"/></svg></div>
  <div class="abs arrow" style="left:1126px;top:237px;background:var(--navy)"><svg width="12" height="12" viewBox="0 0 12 12"><path d="M4 1l5 5-5 5" stroke="#fff" stroke-width="2" fill="none"/></svg></div>
  <div class="course" style="left:96px;top:151px"><div class="ring"><div role="img" aria-label="Worker fastening a safety harness" style="background:linear-gradient(135deg,#d98a2a,#5a5048)"></div></div><h3>Safety Training</h3><span class="book">BOOK NOW</span></div>
  <div class="course" style="left:352px;top:151px"><div class="ring"><div role="img" aria-label="Haul truck at a coal mine" style="background:linear-gradient(135deg,#7c756a,#2e2b26)"></div></div><h3>Coal Mine Training</h3><span class="book">BOOK NOW</span></div>
  <div class="course" style="left:607px;top:151px"><div class="ring"><div role="img" aria-label="Operator working at a machine control panel" style="background:linear-gradient(135deg,#9aa0a3,#3d3f42)"></div></div><h3>Plant Operator<br>Training</h3><span class="book">BOOK NOW</span></div>
  <div class="course" style="left:863px;top:151px"><div class="ring"><div role="img" aria-label="Workers in hi-vis on a worksite" style="background:linear-gradient(135deg,#c6d4dc,#d4862e)"></div></div><h3>High Risk Licences</h3><span class="book">BOOK NOW</span></div>
</section>

<h2 class="abs sec-title" style="left:112px;top:2197px">Onsite / Private<br>Courses</h2>
<p class="abs para" style="left:112px;top:2310px;width:430px">On-site / private training is a learning method where instructors deliver training programs directly at the company's location or workplace. This approach allows for personalized, hands-on learning experiences tailored to the organization's specific needs, equipment, and processes. It facilitates real-time interaction, immediate feedback, and the opportunity for team-building, making it highly effective for skill development and team cohesion.</p>
<a class="btn" style="left:112px;top:2557px;width:140px;height:46px">Learn More</a>
<div class="photo" role="img" aria-label="Site supervisor in hard hat and hi-vis vest holding a clipboard beside a haul truck" style="left:600px;top:2190px;width:488px;height:428px;background:linear-gradient(120deg,#7a6e5f,#b9ad9b 55%,#8fd07a 80%,#e8e4dc)"></div>

<section class="abs" role="img" aria-label="Mining site tinted yellow" style="left:0;top:2760px;width:1200px;height:400px;background:linear-gradient(180deg,#ecc600,#dfbc0a 60%,#e9c500)">
  <h2 class="abs center" style="left:0;top:78px;width:1200px;font-size:40px;font-weight:700;color:var(--navy);line-height:47px;text-transform:uppercase">Your trusted<br>training partner</h2>
  <p class="abs center" style="left:150px;top:185px;width:900px;font-size:18px;line-height:30px;color:var(--navy);font-weight:500">We assist our clients in their ongoing quest to achieve zero harm by providing them with the highest calibre of health and safety management advice and personalised training.</p>
  <a class="btn btn-outline" style="left:530px;top:270px;width:140px;height:46px;border:none">Contact Us</a>
</section>

<h2 class="abs center" style="left:0;top:3268px;width:1200px;font-size:37px;font-weight:600;color:var(--navy);line-height:48px;text-transform:uppercase">Buy now, pay later with FlexiPay<br>Buy what you love now. Pay later.</h2>
<p class="abs center" style="left:0;top:3385px;width:1200px;font-size:19px;color:#333">Choice and flexibility are on your side. Split your purchases into 4 instalments over 6 weeks.</p>
<p class="abs center rubik" style="left:0;top:3428px;width:1200px;font-size:17px;color:#f0c400;font-weight:500">GIVE AWAY – THUNDERLINE MOTORCYCLE OR A BOAT PACKAGE WORTH $35,000</p>
<p class="abs center" style="left:0;top:3468px;width:1200px;font-size:13.5px;line-height:26px;color:#333">All you have to do is click on the button below and complete a Standard 11 refresher to go into the draw.<br>The winner will be announced at the Harvestline Field Day on Saturday the 22nd of June 2024.</p>
<div class="photo" role="img" aria-label="Excavator silhouetted at sunset" style="left:112px;top:3565px;width:305px;height:213px;background:linear-gradient(180deg,#5c7ca6,#e0a24a 50%,#3a2a1c)"></div>
<div class="photo" role="img" aria-label="Construction worker tying reinforcing steel" style="left:447px;top:3565px;width:305px;height:213px;background:linear-gradient(180deg,#c8d4e0,#6d7680 60%,#3b3c40)"></div>
<div class="photo" role="img" aria-label="Excavator loading a truck on red earth" style="left:783px;top:3565px;width:305px;height:213px;background:linear-gradient(180deg,#e3c3a3,#a9553a 55%,#6e2f1d)"></div>
<a class="btn" style="left:527px;top:3833px;width:146px;height:46px">Learn More</a>

<section class="abs" style="left:0;top:3985px;width:1200px;height:665px;background:var(--cream)">
  <h2 class="abs sec-title center" style="left:0;top:98px;width:1200px">Why choose us?</h2>
  <p class="abs center" style="left:145px;top:170px;width:910px;font-size:16px;line-height:27px;color:#444">Southern Plantskills Academy consultants have come from the same industries that we consult back to. Our wealth of first hand knowledge and experience enables us to make invaluable contributions to all facets of safety and training in your workplace.</p>
</section>
<div class="card" style="left:128px"><div class="icon"><svg width="46" height="46" viewBox="0 0 46 46"><path d="M26 6l12 4v9c0 7-5 11-12 13-7-2-12-6-12-13v-9z" fill="#0c2569"/><path d="M20 19l4 4 7-8" stroke="#f7d000" stroke-width="3" fill="none"/><rect x="6" y="34" width="26" height="8" rx="2" fill="#0c2569"/></svg></div><h3>We are passionate</h3><p>We are passionate about Health and Safety.</p></div>
<div class="card" style="left:452px"><div class="icon"><svg width="46" height="46" viewBox="0 0 46 46"><circle cx="23" cy="16" r="9" fill="#0c2569"/><rect x="19" y="25" width="8" height="6" fill="#0c2569"/><path d="M23 2v3M11 6l2 2M35 6l-2 2M6 16h3M37 16h3" stroke="#0c2569" stroke-width="2"/><path d="M6 42l10-9h14l10 9z" fill="#0c2569"/></svg></div><h3>We are dependable</h3><p>Let us deliver the right training solution for your business.</p></div>
<div class="card" style="left:777px"><div class="icon"><svg width="46" height="46" viewBox="0 0 46 46"><rect x="18" y="6" width="24" height="18" fill="#0c2569"/><path d="M22 19l5-6 4 4 6-7" stroke="#f7d000" stroke-width="2" fill="none"/><circle cx="10" cy="14" r="5" fill="#0c2569"/><path d="M4 42V24c0-3 2-4 6-4h8v5h-6v17z" fill="#0c2569"/></svg></div><h3>Nationally recognised</h3><p>We are accredited to delivery nationally recognised training.</p></div>

<footer class="abs footer">
  <div class="fcol" style="left:112px"><h4>Courses</h4><ul>
    <li><svg width="14" height="14" viewBox="0 0 14 14"><circle cx="7" cy="7" r="7" fill="#f7d000"/><path d="M5 4l3 3-3 3" stroke="#0c2569" stroke-width="1.6" fill="none"/></svg>Full Qualifications</li>
    <li><svg width="14" height="14" viewBox="0 0 14 14"><circle cx="7" cy="7" r="7" fill="#f7d000"/><path d="M5 4l3 3-3 3" stroke="#0c2569" stroke-width="1.6" fill="none"/></svg>High Risk Licencing</li>
    <li><svg width="14" height="14" viewBox="0 0 14 14"><circle cx="7" cy="7" r="7" fill="#f7d000"/><path d="M5 4l3 3-3 3" stroke="#0c2569" stroke-width="1.6" fill="none"/></svg>Plant Operator Tickets</li>
    <li><svg width="14" height="14" viewBox="0 0 14 14"><circle cx="7" cy="7" r="7" fill="#f7d000"/><path d="M5 4l3 3-3 3" stroke="#0c2569" stroke-width="1.6" fill="none"/></svg>Short Courses</li></ul></div>
  <div class="fcol" style="left:376px"><h4>Student Resources</h4><ul>
    <li><svg width="14" height="14" viewBox="0 0 14 14"><circle cx="7" cy="7" r="7" fill="#f7d000"/><path d="M5 4l3 3-3 3" stroke="#0c2569" stroke-width="1.6" fill="none"/></svg>Enrolment Form</li>
    <li><svg width="14" height="14" viewBox="0 0 14 14"><circle cx="7" cy="7" r="7" fill="#f7d000"/><path d="M5 4l3 3-3 3" stroke="#0c2569" stroke-width="1.6" fill="none"/></svg>Student Handbook</li>
    <li><svg width="14" height="14" viewBox="0 0 14 14"><circle cx="7" cy="7" r="7" fill="#f7d000"/><path d="M5 4l3 3-3 3" stroke="#0c2569" stroke-width="1.6" fill="none"/></svg>Support</li>
    <li><svg width="14" height="14" viewBox="0 0 14 14"><circle cx="7" cy="7" r="7" fill="#f7d000"/><path d="M5 4l3 3-3 3" stroke="#0c2569" stroke-width="1.6" fill="none"/></svg>Contact us</li></ul></div>
  <div class="fcol" style="left:662px"><h4>Contact Info</h4><ul>
    <li><svg width="12" height="14" viewBox="0 0 12 14"><path d="M6 0a5 5 0 0 1 5 5c0 4-5 9-5 9S1 9 1 5a5 5 0 0 1 5-5z" fill="#f7d000"/><circle cx="6" cy="5" r="2" fill="#0c2569"/></svg><span class="info"><b>ADDRESS:</b>24 Ridgeway Street, Carrowdale,<br>NSW 2811</span></li>
    <li><svg width="12" height="12" viewBox="0 0 12 12"><path d="M2 1c1-1 2 0 2 1l1 2-1 1c1 2 2 3 4 4l1-1 2 1c1 0 1 2 0 2-1 1-2 1-3 1C4 11 1 8 1 4c0-1 0-2 1-3z" fill="#f7d000"/></svg><span class="info"><b>PHONE:</b>1300 555 014</span></li>
    <li><svg width="13" height="10" viewBox="0 0 13 10"><rect width="13" height="10" rx="1" fill="#f7d000"/><path d="M0 1l6.5 5L13 1" stroke="#0c2569" fill="none"/></svg><span class="info"><b>EMAIL:</b>training@southernplantskills.example</span></li></ul></div>
  <div class="fcol" style="left:948px"><h4>Opening Hours</h4><ul>
    <li><svg width="13" height="13" viewBox="0 0 13 13"><circle cx="6.5" cy="6.5" r="5.5" stroke="#f7d000" stroke-width="2" fill="none"/><path d="M6.5 3.5v3h2" stroke="#f7d000" stroke-width="1.5" fill="none"/></svg><span class="info"><b>MON – FRI:</b>7:30am to 4:30pm</span></li>
    <li><svg width="13" height="13" viewBox="0 0 13 13"><circle cx="6.5" cy="6.5" r="5.5" stroke="#f7d000" stroke-width="2" fill="none"/><path d="M6.5 3.5v3h2" stroke="#f7d000" stroke-width="1.5" fill="none"/></svg><span class="info"><b>SAT &amp; SUN:</b>CLOSED</span></li></ul></div>
</footer>
<div class="fbottom"></div>
<p class="abs copy">© 2024 SOUTHERN PLANTSKILLS ACADEMY &nbsp;|&nbsp; <u>RTO number #50872</u></p>
<div class="social abs" style="left:988px;top:4993px"><span></span><span></span><span></span></div>

</body>
</html>
```